Corvel Tandry - Magazine

Our client would like a magazine designed for a conceptual novelty based on unconventional views on contemporary issues, including; finance, religion, politics etc.!

The novelty includes 1 main article, supporting images and 12 short poems.
We would like the designer to create page vectors, borders, fonts and other layout design elements.

In the first stage of the competition we request:

Magazine layout - 6 pages( 4 article variations based on article content and 2 poem page designs)

We would like to see high impact, striking vectors and design concepts to compliment the article content. See attached bullet point guide to article to help design page themes.

COMPANY INFO
Writer, poet, researcher and commentator. Our client is interested in sharing art and issues he believes in. Our client would like to design one magazine issue first but has a collection of material to produce a series of magazines in the future. So he is looking to establish a potentially long-term partnership with designer(s).

Target Market(s)

Quick and easy to read, coffee time magazine. Target Market: Male 40yrs+, Intellectual, Open Minded.

Industry/Entity Type

Finance

Font styles to use
Serif
Decorative

Requirements
Must have
• Main Article and Poetry: Space for 1 -2 images per page.
A subtle design feature that connects each page.
Primary colors: Jade Green and some Grayscale.
Secondary Colors: 3rd and 4th color open to designers preference.
Page Dimensions : 7.5in height, 7in width.
Articles: Same color theme, different layout and vector choice, same font color and size.
Poetry: Some design creative freedom. Focus on creating a unique title font incorporating the theme of the poem, Poetry TITLE font must be made a feature design element (poem identity)
Font: See Ferrowind Explorer magazine styling
Columns: Single or multiple.
All vectors and images should be sourced from pixel harbor.
Nice to have
• Images/pictures that connect with article topic and align with color theme.
Should not have
• Avoid repetition of page design. To do this follow the idea of each paragraph (see attached breakdown)

```html
<!DOCTYPE html>
<html lang="en">
<head>
<meta charset="utf-8">
<title>Corvel Tandry – Governments Destroy Freedom</title>
<link rel="stylesheet" href="https://fonts.googleapis.com/css2?family=Teko:wght@500;600&family=Titillium+Web:wght@400;600;700&display=swap">
<style>
  :root{
    --jade:#1f6048;
    --jade-bright:#3aa57a;
    --ink:#2b2b2b;
    --paper:#ffffff;
    --desk:#e6e6e6;
    --muted:#555;
  }
  *{box-sizing:border-box;margin:0;padding:0}
  html,body{width:1200px;height:600px;overflow:hidden;background:var(--desk)}
  .spread{position:relative;width:1200px;height:600px}
  .page{position:absolute;top:10px;height:581px;background:var(--paper);overflow:hidden}
  .page--left{left:57px;width:543px}
  .page--right{left:600px;width:544px}
  .body-text{font-family:"Titillium Web",sans-serif;font-size:8.8px;line-height:11.3px;color:var(--ink);text-align:justify;overflow:hidden;position:absolute}
  .body-text p{margin-bottom:4px}
  .dropcap{float:left;font-family:"Titillium Web",sans-serif;font-size:38px;line-height:30px;margin:2px 4px 0 0;color:var(--ink)}
  .title{position:absolute;right:36px;top:14px;font-family:"Teko",sans-serif;font-weight:600;font-size:33px;line-height:32px;color:var(--jade);white-space:nowrap}
  .title-block{position:absolute;left:517px;top:5px;width:26px;height:38px;background:var(--jade-bright)}
  .col-a{left:18px;top:52px;width:248px;height:490px}
  .photo{position:absolute}
  .photo--puppet{left:279px;top:50px;width:264px;height:321px;background:linear-gradient(180deg,#3a3a46 0%,#5a4a48 28%,#a3171c 42%,#8a1418 55%,#4a3c38 75%,#2e2a2a 100%)}
  .caption{position:absolute;left:279px;top:375px;width:264px;font-family:"Titillium Web",sans-serif;font-size:7.4px;line-height:9.4px;text-align:center;color:var(--muted)}
  .col-b{left:279px;top:398px;width:254px;height:150px}
  .folio{position:absolute;top:556px;height:25px;display:flex;align-items:center;font-family:"Titillium Web",sans-serif}
  .folio__date{font-size:9px;font-weight:600;color:var(--ink)}
  .folio__name{font-size:12.5px;font-weight:700;color:var(--jade)}
  .folio__num{width:29px;height:25px;background:var(--jade);color:#fff;font-size:12px;font-weight:600;display:flex;align-items:center;justify-content:center}
  .page--left .folio{right:15px;gap:12px}
  .page--right .folio{left:17px;gap:10px}
  .running-bar{position:absolute;left:17px;top:0;width:69px;height:23px;background:var(--jade)}
  .running-head{position:absolute;left:94px;top:5px;font-family:"Teko",sans-serif;font-weight:500;font-size:14px;line-height:14px;color:var(--jade);letter-spacing:.3px}
  .col-c{left:17px;top:40px;width:504px;height:200px}
  .photo--parties{left:17px;top:244px;width:504px;height:308px;background:radial-gradient(ellipse at 50% 60%,#ffffff 0%,#f3f3f3 55%,#e4e6ea 100%)}
</style>
</head>
<body>
<div class="spread">

  <section class="page page--left">
    <h1 class="title">GOVERNMENTS DESTROY FREEDOM</h1>
    <div class="title-block"></div>

    <div class="body-text col-a">
      <p><span class="dropcap">T</span>he first thing to know about governments is that they are not there to serve the interests of the people. They are structured with one thing in mind – control of the people. Once you understand that, everything else comes into focus, such as why governments constantly act in the interests of Big Banking, Big Business, Big Pharma, Big Biotech, and their associated organizations and personnel, and against the interests of the population. How would it be any other way when the same network that owns the ‘Bigs’ also owns the governments and any political party with any chance of forming a government? Life’s a lot less complicated when you see what’s going on.</p>
      <p>There came a time when the people rebelled against rule by royal dictatorship and demanded a say in who ran their country. So the old elites began the process of replacing the overt royal dictatorships with one that had the appearance of freedom while being business as usual.</p>
      <p>Tyranny you could see was replaced with the much more effective tyranny that you can’t see – at least for most people, anyway. The elite’s worst nightmare was for people to be elected to government who were genuinely independent and had the best interests of the population at heart.</p>
      <p>Their solution was to introduce the concept of political parties and they created a structure which, through funding and organization, gave those who did not join one of these parties virtually no hope of being elected to parliament and certainly not forming a government in association with other genuine independent people. You want to go into politics? Okay, pick a party.</p>
      <p>Structure is vital to the control of the many by the few. The formation of political parties produced the structure through which members of parliaments, and those at other levels of government – local and state – could be controlled. Instead of having to force their will upon hundreds of individuals, all they had to do was force it upon those who controlled the parties and they, in turn, would enforce it upon their members.</p>
      <p>Quite simply, if you want to progress in politics you first need to join a party and then keep the ruling elite of that party as happy as you can by what you do and say. As with</p>
    </div>

    <div class="photo photo--puppet" role="img" aria-label="Photo collage: a puppeteer's hands holding strings over a red curtain, above a president speaking to a crowded legislative chamber"></div>
    <p class="caption">Dorran Vale – just like all the other presidents of the past – is just a puppet to the Halverns. This is why the agenda continues…</p>

    <div class="body-text col-b">
      <p>doctors, lawyers, scientists and teachers, you must keep your head down, don’t rock the boat, and certainly don’t oppose anything significant through personal conscience that is against the wishes of your party establishment. Real ‘progress’ in any of these professions demands that you close your mind or sell your soul. Preferably both.</p>
      <p>As the saying goes, it doesn’t matter who you vote for, the government still gets in. Yes, the Halvern government through the control of any party that has a chance of winning office, and many who don’t, but can influence policy and opinion. If you don’t like Halvern-controlled Dorran Vale, then vote for Halvern-</p>
    </div>

    <div class="folio">
      <span class="folio__date">Decembr2013</span>
      <span class="folio__name">Corvel Tandry</span>
      <span class="folio__num">41</span>
    </div>
  </section>

  <section class="page page--right">
    <div class="running-bar"></div>
    <div class="running-head">GOVERNMENTS DESTROY FREEDOM</div>

    <div class="body-text col-c">
      <p>controlled Kessler Brandt. Left or Right? Republican or Democrat? Democracy is a fraud and it’s time to call it what it is. Yes, there are alternative parties we can choose, but as long as the Major Media projects only the two top parties ‘head to head’ with each other splashed all over the news, radio or magazines, then most of the population will only vote for one of those parties. The administration then changes, but their controllers don’t, and the agendas continue as it always had.</p>
      <p>For months prior to Dorran Vale’s majority win, his campaign was all about ‘Change’. Now we can all see that was just a farce and very little ‘changed’ at all. Why? It was all an illusion to campaign for enough voters to get him in, and once he was, there was free reign to continue what the backers wanted – to continue centralizing control through deregulation in line with what the Halverns and other powerful networks are currently working on all around the world. It is building up the structure of a world government, world army, world central bank, world currency and a microchipped population connected to a global computer system and the global positioning satellite network.</p>
      <p>With absolutely no change to their high level of global governance, this structure is building up fast. All our eyes and minds are focused on this Left / Right paradigm and so it’s time to break free from this spell. Is this our only diversion to face? Absolutely not. Little did we ever realize that one sector in our society is all about diversion. So now it’s time to look at the entertainment industry like we’ve never looked at it before…</p>
    </div>

    <div class="photo photo--parties" role="img" aria-label="Illustration: a red, white and blue elephant and donkey balanced on opposite ends of a seesaw"></div>

    <div class="folio">
      <span class="folio__num">42</span>
      <span class="folio__name">Corvel Tandry</span>
      <span class="folio__date">December2013</span>
    </div>
  </section>

</div>
</body>
</html>
```